Diverse, up-scale salon needs eye-catching, unique business cards.

We are looking for a unique business card design for our stylist but that can also be multi functional and used for appointment reminder and referrals. I will need a design in a format that I can modify names and titles going forward. In the past we have had a dark background with the logo on one side, and stylist and contact information on the other but we are open to all ideas. I have included our mission statement as well as branded colors below. The statement doesn't need to go on the card, it's just a reference for target market. We need space for the stylists name, title, instagram handle and then the salons phone number, website and address. I am also open to adding a spot for a qr code linked to the stylist instagram or the salon booking link.

primary brand colors:
#333333 #233415 #36502a #93874a #000000
Mission statement:
Vessolin Hair Studio, a high-end salon located in the lively Downtown Farmington, Michigan, is committed to providing exceptional services in a welcoming and relaxed environment to meet the needs of our diverse clientele.
Our salon specializes in contemporary custom haircuts, coloring, extensions, and barbering and beard grooming services. Our team of skilled stylists is passionate and inventive in their hair styling techniques. At the heart of our salon are values centered on quality, innovation, creativity, and above all, comfort. These core values are evident in every appointment across our customizable array of services.
Our goal is to establish a benchmark for exceptional hair care for every human.
Website: www.vessolinhairstudio.example
instagram: @vessolinhairstudio
address: 41782 Pelham Crest Rd, Farmington MI
phone: 248-613-4087

Industry/Entity Type

Hair Salon

Contact Information for Business Card

Stylist name, title, phone, instagram, website, address, (optional qr code)

Requirements
Should not have
• Does not need mission statement on the card.

```html
<!DOCTYPE html>
<html lang="en">
<head>
<meta charset="utf-8">
<title>Vessolin Hair Studio – Business Card</title>
<link href="https://fonts.googleapis.com/css2?family=Open+Sans:wght@400;700&display=swap" rel="stylesheet">
<style>
  :root {
    --stage: #222222;
    --card-black: #141414;
    --gold: #93874a;
    --gold-light: #a3965a;
    --white: #ffffff;
  }
  * { box-sizing: border-box; margin: 0; padding: 0; }
  html, body { width: 1200px; height: 780px; overflow: hidden; }
  body {
    background: var(--stage);
    font-family: "Open Sans", Arial, sans-serif;
    position: relative;
  }
  .card {
    position: absolute;
    width: 560px;
    height: 320px;
    border-radius: 22px;
    overflow: hidden;
    top: 230px;
  }
  .card--back { left: 26px; }
  .card--front { left: 614px; background: var(--card-black); }

  .pattern-fill {
    width: 100%;
    height: 100%;
    background: radial-gradient(circle at 40% 35%, var(--gold-light), var(--gold) 70%);
  }

  .band {
    position: absolute;
    left: 0; right: 0;
    top: 66px;
    height: 86px;
    background: var(--gold);
  }
  .brand-mark {
    position: absolute;
    left: 200px;
    top: 30px;
    width: 160px;
    height: 160px;
    border-radius: 50%;
    background: var(--card-black);
    border: 3px solid var(--gold);
    box-shadow: 0 0 0 8px var(--card-black);
    display: flex;
    align-items: center;
    justify-content: center;
    text-align: center;
  }
  .brand-name {
    color: var(--gold);
    font-weight: 700;
    font-size: 17px;
    line-height: 1.25;
    letter-spacing: 2px;
    text-transform: uppercase;
  }

  .stylist {
    position: absolute;
    right: 300px;
    top: 214px;
    text-align: right;
    color: var(--white);
  }
  .stylist-name {
    color: var(--gold);
    font-weight: 700;
    font-size: 22px;
    letter-spacing: 0.5px;
    text-transform: uppercase;
    line-height: 1.1;
  }
  .stylist-title { font-size: 14px; margin-top: 2px; }
  .stylist-address { font-size: 14px; line-height: 1.35; margin-top: 10px; }

  .divider {
    position: absolute;
    left: 279px;
    top: 212px;
    width: 1.5px;
    height: 82px;
    background: var(--gold);
  }

  .contacts {
    position: absolute;
    left: 300px;
    top: 212px;
    list-style: none;
    color: var(--white);
    font-size: 13.5px;
  }
  .contacts li {
    display: flex;
    align-items: center;
    gap: 8px;
    height: 21px;
  }
  .contacts svg { width: 12px; height: 12px; flex: none; }
</style>
</head>
<body>
  <section class="card card--back">
    <div class="pattern-fill" role="img" aria-label="Embossed repeating salon monogram pattern on gold"></div>
  </section>

  <section class="card card--front">
    <div class="band"></div>
    <div class="brand-mark">
      <span class="brand-name">Vessolin<br>Hair Studio</span>
    </div>

    <div class="stylist">
      <p class="stylist-name">Marcus Hale</p>
      <p class="stylist-title">Managing Director</p>
      <p class="stylist-address">41782 Pelham Crest Rd,<br>Farmington MI</p>
    </div>

    <div class="divider"></div>

    <ul class="contacts">
      <li>
        <svg viewBox="0 0 24 24" fill="var(--gold)"><path d="M6.6 10.8a15 15 0 0 0 6.6 6.6l2.2-2.2c.3-.3.7-.4 1-.2 1.1.4 2.3.6 3.6.6.6 0 1 .4 1 1V20c0 .6-.4 1-1 1A17 17 0 0 1 3 4c0-.6.4-1 1-1h3.5c.6 0 1 .4 1 1 0 1.3.2 2.5.6 3.6.1.3 0 .7-.2 1z"/></svg>
        248-613-4087
      </li>
      <li>
        <svg viewBox="0 0 24 24" fill="none" stroke="var(--gold)" stroke-width="2.5"><rect x="2" y="5" width="20" height="14" rx="1"/><path d="M2 6l10 7 10-7"/></svg>
        info@vessolinstudio.example
      </li>
      <li>
        <svg viewBox="0 0 24 24" fill="none" stroke="var(--gold)" stroke-width="2.5"><circle cx="12" cy="12" r="9"/></svg>
        @vessolinhairstudio
      </li>
      <li>
        <svg viewBox="0 0 24 24" fill="none" stroke="var(--gold)" stroke-width="2"><circle cx="12" cy="12" r="10"/><ellipse cx="12" cy="12" rx="4.5" ry="10"/><path d="M2 12h20"/></svg>
        www.vessolinhairstudio.example
      </li>
    </ul>
  </section>
</body>
</html>
```